Budget Brand Responsive Website

Flat vector style website needed for value based IT support company. looking for clean, illustration intensive based design. Current test site can be found at www.bright-mend.co.uk and holding page it www.brightmend.co.uk this will show text and services, please feel free to use placeholder text if you think we need alternative text in places. Emphasis should be on low cost support and services listed on the site, would be nice to see costs in bold images. important colors are the blue, orange and white, see holding page and attached image of an advert

It Company

```html
<!DOCTYPE html>
<html lang="en">
<head>
<meta charset="utf-8">
<title>Bright Mend – IT Services</title>
<link href="https://fonts.googleapis.com/css2?family=Open+Sans:wght@400;600;700;800&display=swap" rel="stylesheet">
<style>
:root{
  --blue:#2d4f8e;
  --blue-dark:#233f73;
  --orange:#e07a2e;
  --ink:#2b2b2b;
  --text:#666;
  --light:#f1f2f4;
  --line:#d9dce1;
  --white:#fff;
}
*{box-sizing:border-box;margin:0;padding:0}
html,body{width:1200px;height:2176px;overflow:hidden}
body{font-family:"Open Sans",Arial,sans-serif;color:var(--text);background:var(--white);position:relative}
.site-header{height:44px;display:flex;align-items:center;justify-content:space-between;padding:0 40px;border-bottom:1px solid var(--line)}
.brand{font-weight:700;font-size:20px;color:var(--ink)}
.main-nav{display:flex;gap:34px;font-size:11px;font-weight:700;color:var(--ink);letter-spacing:.5px}
.main-nav .active{color:var(--orange)}
.hero{position:relative;height:548px}
.hero-art{position:absolute;inset:0;background:linear-gradient(160deg,#f4f5f7 0%,#e6e9ee 55%,#dde1e8 100%)}
.hero-caption{position:absolute;left:40px;top:405px;width:420px;background:rgba(40,44,52,.85);padding:16px 22px;color:var(--white)}
.hero-caption h1{font-size:27px;font-weight:800;letter-spacing:.5px}
.hero-caption p{font-size:13px;margin-top:4px}
.intro{text-align:center;padding:60px 150px 0;height:236px}
.section-title{font-size:30px;font-weight:800;color:var(--ink);text-align:center;letter-spacing:.3px}
.intro p{font-size:12px;line-height:1.7;margin-top:14px}
.intro .call{color:var(--orange);font-weight:700;font-size:14px;margin-top:12px}
.services{height:252px;padding-top:8px}
.service-icons{display:flex;justify-content:space-between;padding:30px 60px 0}
.service{width:170px;text-align:center}
.service-ring{width:62px;height:62px;border:2px solid var(--blue);border-radius:50%;margin:0 auto;display:flex;align-items:center;justify-content:center}
.service h3{font-size:14px;font-weight:800;color:var(--ink);margin-top:12px}
.service p{font-size:10px;line-height:1.5;margin-top:6px}
.packages{background:var(--light);height:412px;display:flex;justify-content:center;gap:28px;padding-top:30px}
.package{width:224px;height:352px;background:var(--white);display:flex;flex-direction:column}
.package-head{background:var(--orange);color:var(--white);text-align:center;padding:10px 8px}
.package-head h3{font-size:16px;font-weight:800}
.package-head p{font-size:10px}
.package-img{height:124px}
.img-support{background:linear-gradient(135deg,#d7dde6,#aab6c9)}
.img-voice{background:linear-gradient(135deg,#e9edf2,#c3ccd9)}
.img-hosting{background:linear-gradient(135deg,#5c6f8c,#c8d2e0)}
.img-cloud{background:linear-gradient(135deg,#dfe6ef,#7f9bc2)}
.prices{flex:1;text-align:center;font-size:12px;line-height:2;padding-top:16px;color:var(--ink)}
.prices b{font-weight:700}
.btn-more{background:var(--blue);color:var(--white);text-align:center;font-size:12px;font-weight:700;padding:11px 0}
.info{display:flex;justify-content:center;gap:40px;padding-top:70px;height:518px}
.info-col{width:320px}
.info-col h2{font-size:21px;font-weight:800;color:var(--ink);white-space:nowrap}
.info-col p{font-size:11px;line-height:1.75;margin-top:14px}
.btn-read{display:inline-block;background:var(--orange);color:var(--white);font-size:11px;font-weight:700;padding:9px 18px;margin-top:26px}
.site-footer{position:absolute;left:0;right:0;top:2010px;height:135px;background:var(--blue);padding:38px 60px 0}
.footer-row{display:flex;align-items:center;justify-content:space-between}
.footer-nav{display:flex;gap:22px;font-size:11px;color:var(--white)}
.footer-nav span+span:before{content:"|";margin-right:22px;opacity:.6}
.social{display:flex;gap:12px}
.social span{width:30px;height:30px;border-radius:50%;background:var(--blue-dark);border:1px solid rgba(255,255,255,.4)}
.copyright{font-size:10px;color:var(--white);margin-top:40px}
.bottom-bar{position:absolute;left:0;right:0;top:2145px;height:31px;background:var(--blue-dark);border-top:3px solid var(--orange)}
</style>
</head>
<body>
<header class="site-header">
  <div class="brand">Bright Mend</div>
  <nav class="main-nav"><span class="active">HOME</span><span>SUPPORT</span><span>SERVICES</span><span>ABOUT</span><span>CONTACT</span></nav>
</header>

<section class="hero">
  <div class="hero-art" role="img" aria-label="Flat illustration of an office desk seen from above with laptop, tablet, phone, coffee cup and charts"></div>
  <div class="hero-caption">
    <h1>IT SERVICES THE FAIR WAY</h1>
    <p>We help our clients increase productivity while reducing cost</p>
  </div>
</section>

<section class="intro">
  <h2 class="section-title">DON'T GET TIED DOWN!</h2>
  <p>Bright Mend gives small businesses friendly, flexible IT support at a fair price. No long contracts, no hidden fees and no jargon – just reliable help when you need it. Choose the services that suit your team, scale up or down as you grow, and let our engineers keep your systems running smoothly every day.</p>
  <p class="call">CALL US TODAY ON 01632 960 000</p>
</section>

<section class="services">
  <h2 class="section-title">SERVICES TAILORED FOR YOU</h2>
  <div class="service-icons">
    <div class="service"><div class="service-ring"><svg width="30" height="30" viewBox="0 0 30 30" fill="none" stroke="#2d4f8e" stroke-width="2"><circle cx="15" cy="10" r="5"/><path d="M5 27c0-6 4-9 10-9s10 3 10 9"/></svg></div><h3>SUPPORT</h3><p>Unlimited remote support and monitoring for your team.</p></div>
    <div class="service"><div class="service-ring"><svg width="30" height="30" viewBox="0 0 30 30" fill="none" stroke="#2d4f8e" stroke-width="2"><path d="M8 4l5 5-3 3c1 3 4 6 7 7l3-3 5 5-3 4C13 25 5 17 4 7z"/></svg></div><h3>VOICE</h3><p>Business lines, calls and bundles with clear pricing.</p></div>
    <div class="service"><div class="service-ring"><svg width="30" height="30" viewBox="0 0 30 30" fill="none" stroke="#2d4f8e" stroke-width="2"><circle cx="15" cy="15" r="11"/><path d="M4 15h22M15 4c4 4 4 18 0 22M15 4c-4 4-4 18 0 22"/></svg></div><h3>INTERNET</h3><p>Fast, dependable broadband and fibre for any office.</p></div>
    <div class="service"><div class="service-ring"><svg width="30" height="30" viewBox="0 0 30 30" fill="none" stroke="#2d4f8e" stroke-width="2"><rect x="7" y="13" width="16" height="13"/><path d="M10 13V9a5 5 0 0 1 10 0v4"/></svg></div><h3>SECURITY</h3><p>Antivirus, firewalls and backups keeping data safe.</p></div>
    <div class="service"><div class="service-ring"><svg width="30" height="30" viewBox="0 0 30 30" fill="none" stroke="#2d4f8e" stroke-width="2"><rect x="6" y="5" width="18" height="8"/><rect x="6" y="17" width="18" height="8"/><path d="M10 9h2M10 21h2"/></svg></div><h3>HOSTING</h3><p>Simple, secure hosting for websites and email.</p></div>
    <div class="service"><div class="service-ring"><svg width="30" height="30" viewBox="0 0 30 30" fill="none" stroke="#2d4f8e" stroke-width="2"><path d="M8 22h15a5 5 0 0 0 0-10 7 7 0 0 0-13-1 5.5 5.5 0 0 0-2 11z"/></svg></div><h3>CLOUD</h3><p>Online storage and tools to work from anywhere.</p></div>
  </div>
</section>

<section class="packages">
  <article class="package">
    <div class="package-head"><h3>SUPPORT</h3><p>Unlimited Remote Support</p></div>
    <div class="package-img img-support" role="img" aria-label="Photo of a support team at work"></div>
    <div class="prices">Workstations <b>£5.00</b><br>Users <b>£8.00</b><br>Servers <b>£25.00</b></div>
    <div class="btn-more">MORE</div>
  </article>
  <article class="package">
    <div class="package-head"><h3>VOICE</h3><p>Lines, calls and call bundles</p></div>
    <div class="package-img img-voice" role="img" aria-label="Photo of an office desk phone"></div>
    <div class="prices">Workstations <b>£4.00</b><br>Users <b>£6.00</b><br>Servers <b>£20.00</b></div>
    <div class="btn-more">MORE</div>
  </article>
  <article class="package">
    <div class="package-head"><h3>HOSTING</h3><p>Simple and Secure</p></div>
    <div class="package-img img-hosting" role="img" aria-label="Photo of a server room corridor"></div>
    <div class="prices">Workstations <b>£3.00</b><br>Users <b>£5.00</b><br>Servers <b>£30.00</b></div>
    <div class="btn-more">MORE</div>
  </article>
  <article class="package">
    <div class="package-head"><h3>CLOUD</h3><p>Online Data &amp; Secure Technology</p></div>
    <div class="package-img img-cloud" role="img" aria-label="Illustration of connected cloud services"></div>
    <div class="prices">Workstations <b>£4.00</b><br>Users <b>£7.00</b><br>Servers <b>£22.00</b></div>
    <div class="btn-more">MORE</div>
  </article>
</section>

<section class="info">
  <div class="info-col">
    <h2>ABOUT BRIGHT MEND</h2>
    <p>Bright Mend is a friendly IT support company for small and growing businesses. Our engineers provide fast remote help, on-site visits and proactive monitoring, so problems are solved before they slow you down.</p>
    <p>We believe good IT support should be affordable for everyone. That is why our prices are clear, our contracts are flexible and our team always explains things in plain English.</p>
  </div>
  <div class="info-col">
    <h2>WE EXCEED EXPECTATIONS</h2>
    <p>From the first call we aim to go further than you expect. We learn how your business works, recommend only what you need and keep your systems secure, updated and running at their best.</p>
    <p>Our clients stay with us because we answer quickly, fix things properly and treat every request with care, whether it is a single laptop or a whole office network.</p>
  </div>
  <div class="info-col">
    <h2>TECHNICAL SUPPORT</h2>
    <p>Our helpdesk team is ready to assist by phone, email or remote session. We cover hardware, software, networks and email, with clear updates from start to finish.</p>
    <p>Need someone on site? Our engineers can visit your premises to install, repair or upgrade equipment at a time that suits you.</p>
    <span class="btn-read">READ MORE</span>
  </div>
</section>

<footer class="site-footer">
  <div class="footer-row">
    <nav class="footer-nav"><span>Home</span><span>Support</span><span>Services</span><span>About</span><span>Contact</span></nav>
    <div class="social"><span></span><span></span><span></span><span></span></div>
  </div>
  <p class="copyright">Copyright © 2015 Bright Mend</p>
</footer>
<div class="bottom-bar"></div>
</body>
</html>
```